Keystone Coaching Roadmap

I've included a mock up of what I like. This design needs to be made better. I like the top section layout. It needs 5 circles for:

Please create a webpage based on this design, but improve it. Use the letterhead and business card brand you created for me to make the brand look seamless.

I love the circles - please make 5 of them the same size (can be 1 lines)

Here is the text for the circles:

Headline: Your Guided Path to Transformation
Text
Step 1: The Initial Consultation
text
Step 2: Deep-Dive Discovery and Assessment
text
Step 3: Synthesis and Strategy Formulation
text
Step 4: The Strategic Debrief Session
Text
Step 5: Implementation and Ongoing Support
Text

Also, there are many sections to this page including:

Introduction
Copy
Copy
Bio
CTA
FAQ's

Please make it interesting.

Use the colors of the mockup and my website: Corwin Adeley.com
I am including my letterhead and business card for brand coherence.

Use the fonts on my website. CorwinAdeley.com

I will need all files to send to the developer. We must have ALL the art files.

see my website; CorwinAdeley.com

See my uploads

Must have
• all the design files

```html
<!DOCTYPE html>
<html lang="en">
<head>
<meta charset="utf-8">
<title>Keystone Coaching — Elite Coaching</title>
<link rel="stylesheet" href="https://fonts.googleapis.com/css2?family=Lexend:wght@400;500&family=Open+Sans:wght@400;600&display=swap">
<style>
:root{
  --navy:#141a3c;
  --navy-deep:#0e1330;
  --gold:#a88a57;
  --gold-light:#c9ab78;
  --gold-dark:#7d6339;
  --teal:#2b6e86;
  --mist:#eceef3;
  --ink:#1d1f2a;
  --body:#3e4150;
  --white:#ffffff;
}
*{box-sizing:border-box;margin:0;padding:0}
html,body{width:1200px;height:5111px;overflow:hidden}
body{position:relative;background:var(--white);font-family:"Open Sans",Arial,sans-serif;color:var(--body)}
.abs{position:absolute}
h1,h2,h3{font-family:"Lexend",Helvetica,sans-serif;font-weight:400;color:var(--ink)}
p{font-size:14px;line-height:25px}
.btn{position:absolute;display:inline-flex;align-items:center;gap:6px;height:36px;padding:0 18px;border-radius:8px;background:var(--gold);color:#fff;font-size:14px;font-family:"Open Sans",Arial,sans-serif;text-decoration:none;box-shadow:0 2px 6px rgba(0,0,0,.15)}
.btn::after{content:"»";font-size:16px}

/* wordmark */
.wordmark{position:absolute;display:flex;align-items:center;gap:10px;font-family:"Lexend",Helvetica,sans-serif;font-weight:400;white-space:nowrap}
.wordmark-dot{border-radius:50%;border:2px solid currentColor;flex:none}

/* header */
.site-header{position:absolute;left:0;top:0;width:1200px;height:100px;background:#fff;border-bottom:1px solid #ddd}
.site-header .wordmark{left:76px;top:30px;color:var(--navy);font-size:18px}
.site-header .wordmark-dot{width:38px;height:38px}
.main-nav{position:absolute;right:72px;top:38px;display:flex;gap:34px;font-size:15px;color:#444}
.main-nav .active{color:var(--ink);font-weight:600;border-bottom:2px solid var(--ink)}

/* hero */
.hero-photo{position:absolute;left:0;top:100px;width:1200px;height:680px;background:linear-gradient(100deg,#e9ecf1 0%,#cfd4dc 32%,#7d7c82 55%,#3a3c4a 78%,#2a2c3a 100%)}
.hero h1{position:absolute;left:76px;top:168px;font-size:44px;line-height:54px;color:var(--navy);font-weight:400}
.hero .lead{position:absolute;left:77px;top:345px;font-size:17px;line-height:26px;color:var(--ink)}

/* bio */
.bio-photo-ring{position:absolute;left:98px;top:790px;width:468px;height:468px;border-radius:50%;border:5px solid var(--gold)}
.bio-photo{position:absolute;left:122px;top:780px;width:420px;height:420px;border-radius:50%;background:radial-gradient(circle at 50% 40%,#c7b2a2,#58505a 60%,#1c2138)}
.bio h2{position:absolute;left:628px;top:832px;font-size:36px}
.bio .copy{position:absolute;left:632px;top:904px;width:478px;font-size:14px;line-height:25.5px}
.bio .copy p+p{margin-top:4px}

/* path */
.path{position:absolute;left:0;top:1346px;width:1200px;height:518px;background:radial-gradient(ellipse at 50% 30%,#1e2550,var(--navy-deep) 70%)}
.path h2{position:absolute;left:0;top:78px;width:1200px;text-align:center;color:#fff;font-size:35px;line-height:46px}
.step{position:absolute;top:214px;width:210px;text-align:center}
.step-ring{width:156px;height:156px;margin:0 auto;border-radius:50%;background:conic-gradient(var(--gold-light) 0 25%,var(--gold) 25% 50%,var(--gold-dark) 50% 75%,var(--gold) 75%);display:flex;align-items:center;justify-content:center}
.step-core{width:114px;height:114px;border-radius:50%;background:var(--gold);border:4px solid #f1e6d2;display:flex;align-items:center;justify-content:center}
.step-label{margin-top:20px;font-family:"Lexend",Helvetica,sans-serif;color:#fff;font-size:16px;line-height:20px}
.arrow{position:absolute;top:284px}

/* seeking */
.seek h2{position:absolute;left:110px;top:1938px;width:960px;font-size:35px;line-height:44px}
.seek .copy{position:absolute;left:110px;top:2104px;width:478px;font-size:13.5px;line-height:25.5px}
.seek .copy p+p{margin-top:6px}
.chess-art{position:absolute;left:566px;top:2066px;width:524px;height:356px;background:radial-gradient(ellipse at 60% 50%,rgba(168,138,87,.18),rgba(255,255,255,0) 65%)}

/* stats */
.mist{position:absolute;left:0;top:2600px;width:1200px;height:1512px;background:var(--mist)}
.stats{position:absolute;left:112px;top:2510px;width:976px;height:184px;border-radius:24px;background:linear-gradient(120deg,var(--navy-deep),#1e2655 60%,var(--navy-deep));display:flex;align-items:center}
.stat{text-align:center;color:#fff;position:relative}
.stat .num{font-family:"Lexend",Helvetica,sans-serif;font-size:24px;margin-top:14px}
.stat .lbl{font-size:14px}
.stat-div{width:1px;height:92px;background:rgba(255,255,255,.5)}

/* benefits */
.benefits h2{position:absolute;left:0;top:2772px;width:1200px;text-align:center;font-size:35px;line-height:44px}
.benefits .intro{position:absolute;left:120px;top:2890px;width:960px;text-align:center;font-size:14px;line-height:25.5px}
.card{position:absolute;top:3018px;width:228px;height:360px;border:2px solid #c8c8cc;border-radius:10px;background:#fff;padding:10px 10px 0;text-align:center}
.card h3{font-size:19px;line-height:24px;margin-bottom:14px;color:var(--ink)}
.card p{font-size:11.5px;line-height:21.5px;color:#555}
.card .more{position:absolute;left:14px;bottom:14px;width:196px;height:36px;border-radius:8px;background:var(--gold);color:#fff;font-size:14px;display:flex;align-items:center;justify-content:center;gap:6px}
.card .more::after{content:"»"}
.card.featured{background:linear-gradient(180deg,var(--gold-light),var(--gold-dark));border-color:var(--gold)}
.card.featured h3,.card.featured p{color:#fff}
.card.featured .more{background:#fff;color:var(--ink)}

.rule{position:absolute;left:112px;top:3464px;width:976px;height:1px;background:#777}

/* closing */
.closing h2{position:absolute;left:112px;top:3594px;font-size:35px;line-height:44px;font-weight:400}
.closing .copy{position:absolute;left:112px;top:3748px;width:478px;font-size:14.5px;line-height:26px}
.closing-ring{position:absolute;left:634px;top:3556px;width:468px;height:468px;border-radius:50%;border:5px solid var(--gold)}
.closing-photo{position:absolute;left:660px;top:3582px;width:420px;height:420px;border-radius:50%;background:radial-gradient(circle at 62% 38%,#c9b1a0,#5a4a4c 45%,#1c2138 75%)}

/* faq */
.faq h2{position:absolute;left:0;top:4186px;width:1200px;text-align:center;font-size:35px}
.faq .intro{position:absolute;left:250px;top:4268px;width:700px;text-align:center;font-size:15px;line-height:26px}
.q{position:absolute;left:195px;width:810px;height:38px;border:1.5px solid #999;border-radius:8px;font-size:13px;padding:0 18px;display:flex;align-items:center;justify-content:space-between;color:#333}
.q::after{content:"";width:7px;height:7px;border-right:2px solid #444;border-bottom:2px solid #444;transform:rotate(45deg) translateY(-3px)}
.q.open{background:var(--gold);border-color:var(--gold);color:#fff;border-radius:8px 8px 0 0}
.q.open::after{border-color:#fff;transform:rotate(-135deg)}
.answer{position:absolute;left:195px;top:4458px;width:810px;height:64px;border:1.5px solid #999;border-top:none;border-radius:0 0 8px 8px;padding:10px 40px;font-size:13px;line-height:24px;color:#333}

/* footer */
.footer{position:absolute;left:0;top:4720px;width:1200px;height:391px}
.foot-brand.wordmark{left:0;top:4930px;width:1200px;justify-content:center;color:#fff;font-size:22px}
.foot-brand .wordmark-dot{width:48px;height:48px}
.foot-nav{position:absolute;left:0;top:5022px;width:1200px;display:flex;justify-content:center;gap:40px;color:#fff;font-size:17px}
.foot-rule{position:absolute;left:112px;top:5070px;width:976px;height:1px;background:rgba(255,255,255,.35)}
.copyright{position:absolute;left:112px;top:5086px;font-size:12px;color:#c9cbd6}
.social{position:absolute;left:1070px;top:5084px;width:18px;height:18px;border-radius:50%;background:#fff}
</style>
</head>
<body>

<header class="site-header">
  <div class="wordmark"><span class="wordmark-dot"></span><span>Keystone Coaching</span></div>
  <nav class="main-nav"><span class="active">Home</span><span>Coaching</span><span>Retreats</span><span>About</span><span>Insights</span><span>FAQs</span><span>Contact</span></nav>
</header>

<section class="hero">
  <div class="hero-photo" role="img" aria-label="Photo of a confident team of business leaders standing above a city skyline"></div>
  <svg class="abs" style="left:0;top:590px" width="1200" height="200" viewBox="0 0 1200 200" aria-hidden="true">
    <path d="M0 80 Q600 0 1200 185 L1200 200 L0 200Z" fill="var(--gold)"/>
    <path d="M0 120 Q500 20 1200 190 L1200 200 L0 200Z" fill="var(--teal)"/>
    <path d="M0 150 Q600 60 1200 200 L0 200Z" fill="#fff"/>
  </svg>
  <h1>Support Your<br>Leadership Efforts with<br>Elite Coaching</h1>
  <p class="lead">Introducing Elite Leadership Coaching and<br>Organization Development</p>
  <a class="btn" style="left:77px;top:426px">Book A Discovery Call</a>
</section>

<section class="bio">
  <div class="bio-photo-ring"></div>
  <div class="bio-photo" role="img" aria-label="Portrait photo of coach Corwin Adeley"></div>
  <h2>Corwin Adeley</h2>
  <div class="copy">
    <p>As a top leader, you deserve an elite partnership designed exclusively for you—especially when you need a partner you can count on. With a perspective rooted in both wisdom and empathy, I offer insights, intuition, and support that many other coaches simply cannot replicate.</p>
    <p>My mission is to guide high-performing leaders and their teams toward a state of peak performance defined by stress-free resilience, heightened productivity, and effortless flow. I founded Corwin Adeley International to provide effective, accelerated training that unlocks the highest levels of human potential.</p>
  </div>
  <a class="btn" style="left:632px;top:1186px">Book A Discovery Call</a>
</section>

<section class="path">
  <h2>Your Guided<br>Path To Transformation</h2>
  <div class="step" style="left:83px"><div class="step-ring"><div class="step-core"><svg width="54" height="54" viewBox="0 0 54 54" aria-hidden="true"><circle cx="27" cy="27" r="14" fill="none" stroke="#fff" stroke-width="5" stroke-dasharray="6 4"/><circle cx="27" cy="27" r="6" fill="#fff"/></svg></div></div><div class="step-label">The Initial<br>Consultation</div></div>
  <svg class="arrow" style="left:280px" width="24" height="16" aria-hidden="true"><path d="M2 8H20M14 2L20 8L14 14" stroke="#fff" stroke-width="2.5" fill="none"/></svg>
  <div class="step" style="left:290px"><div class="step-ring"><div class="step-core"><svg width="54" height="54" viewBox="0 0 54 54" aria-hidden="true"><rect x="12" y="8" width="30" height="38" rx="3" fill="none" stroke="#fff" stroke-width="3"/><path d="M18 20H36M18 28H36M18 36H30" stroke="#fff" stroke-width="3"/></svg></div></div><div class="step-label">Deep-Dive Discovery<br>&amp; Assessment</div></div>
  <svg class="arrow" style="left:485px" width="24" height="16" aria-hidden="true"><path d="M2 8H20M14 2L20 8L14 14" stroke="#fff" stroke-width="2.5" fill="none"/></svg>
  <div class="step" style="left:495px"><div class="step-ring"><div class="step-core"><svg width="54" height="54" viewBox="0 0 54 54" aria-hidden="true"><circle cx="27" cy="31" r="13" fill="none" stroke="#fff" stroke-width="4"/><path d="M27 4V16M21 10H33" stroke="#fff" stroke-width="3"/></svg></div></div><div class="step-label">Synthesis &amp;<br>Strategy Formulation</div></div>
  <svg class="arrow" style="left:690px" width="24" height="16" aria-hidden="true"><path d="M2 8H20M14 2L20 8L14 14" stroke="#fff" stroke-width="2.5" fill="none"/></svg>
  <div class="step" style="left:700px"><div class="step-ring"><div class="step-core"><svg width="54" height="54" viewBox="0 0 54 54" aria-hidden="true"><rect x="8" y="10" width="38" height="26" rx="2" fill="none" stroke="#fff" stroke-width="3"/><path d="M27 36V46M18 46H36" stroke="#fff" stroke-width="3"/></svg></div></div><div class="step-label">The Strategic<br>Debrief Session</div></div>
  <svg class="arrow" style="left:895px" width="24" height="16" aria-hidden="true"><path d="M2 8H20M14 2L20 8L14 14" stroke="#fff" stroke-width="2.5" fill="none"/></svg>
  <div class="step" style="left:907px"><div class="step-ring"><div class="step-core"><svg width="54" height="54" viewBox="0 0 54 54" aria-hidden="true"><circle cx="27" cy="18" r="7" fill="#fff"/><circle cx="13" cy="24" r="5" fill="#fff"/><circle cx="41" cy="24" r="5" fill="#fff"/><path d="M14 44Q27 24 40 44Z" fill="#fff"/></svg></div></div><div class="step-label">Implementation<br>&amp; Ongoing Support</div></div>
</section>

<section class="seek">
  <h2>Are you seeking a Leadership Coach &amp; Organization Development Specialist to Elevate your leadership impact?</h2>
  <div class="copy">
    <p>Elite Coaching with Corwin Adeley — Your organization—and its challenges—are unlike any other. Generic training can only take your leaders so far. To achieve the profound, lasting impact your vision demands, you need a solution crafted specifically for you.</p>
    <p>Corwin Adeley creates transformative, custom leadership retreats for management teams in the Greater Seattle Area. Through Elite Coaching, we provide the deep guidance and tailored strategies your leaders need to overcome obstacles, foster unity, and achieve exceptional, lasting results—only possible through a uniquely designed, custom-built program.</p>
  </div>
  <a class="btn" style="left:110px;top:2386px">Book A Discovery Call</a>
  <div class="chess-art" role="img" aria-label="Gold line illustration of a chess king toppling a queen"></div>
</section>

<div class="mist"></div>
<div class="stats">
  <div class="stat" style="width:205px"><svg width="60" height="56" aria-hidden="true"><path d="M10 44Q30 54 50 40M30 8L34 18L44 18L36 25L39 35L30 29L21 35L24 25L16 18L26 18Z" stroke="var(--gold-light)" stroke-width="2" fill="none"/></svg><div class="num">25 Years</div><div class="lbl">Experience</div></div>
  <div class="stat-div"></div>
  <div class="stat" style="width:260px"><svg width="60" height="56" aria-hidden="true"><rect x="8" y="8" width="44" height="32" rx="2" stroke="var(--gold-light)" stroke-width="2" fill="none"/><path d="M12 50H48" stroke="var(--gold-light)" stroke-width="2"/></svg><div class="num">1,500+</div><div class="lbl">Transformational Sessions</div></div>
  <div class="stat-div"></div>
  <div class="stat" style="width:200px"><svg width="60" height="56" aria-hidden="true"><path d="M30 6L52 16V42L30 52L8 42V16Z M8 16L30 26L52 16 M30 26V52" stroke="var(--gold-light)" stroke-width="2" fill="none"/></svg><div class="num">#1 Riverbook</div><div class="lbl">Bestselling Author</div></div>
  <div class="stat-div"></div>
  <div class="stat" style="width:300px"><svg width="60" height="56" aria-hidden="true"><rect x="14" y="4" width="32" height="40" rx="2" stroke="var(--gold-light)" stroke-width="2" fill="none"/><path d="M20 14H40M20 22H40M20 30H32" stroke="var(--gold-light)" stroke-width="2"/></svg><div class="num">700+</div><div class="lbl">Licensable Training Materials</div></div>
</div>

<section class="benefits">
  <h2>Core Benefits of<br>Elite Coaching for Leaders</h2>
  <p class="intro">Elite coaching provides a confidential, strategic partnership designed to elevate the performance of top executives and their organizations. This bespoke service focuses on the specific, high-stakes challenges that leaders face. Below is an expansion of the core benefits you can expect from this exclusive engagement.</p>
  <div class="card" style="left:112px"><h3>Exclusivity &amp; Tailored Strategies</h3><p>This is not a one-size-fits-all program. Your coaching experience is designed exclusively for you, your leadership style, and your organization's unique circumstances. We develop a completely customized roadmap that addresses your specific goals and challenges.</p><span class="more">Read More</span></div>
  <div class="card" style="left:362px"><h3>Strategic<br>Decision-Making</h3><p>As a leader, you face complex decisions with far-reaching consequences. Elite coaching provides a confidential sounding board to pressure-test ideas, explore potential outcomes, and gain clarity on the best path forward. We work together to sharpen your analytical skills, enhance your foresight.</p><span class="more">Read More</span></div>
  <div class="card featured" style="left:612px"><h3>Leadership<br>Development</h3><p>Even the most accomplished leaders have room to grow. This coaching focuses on refining your unique leadership capabilities, whether that means enhancing your executive presence, inspiring high-performing teams, or leading transformative change. We identify and amplify</p><span class="more">Read More</span></div>
  <div class="card" style="left:862px"><h3>Navigating<br>Organizational</h3><p>From internal politics and cultural shifts to external market disruptions, leaders must steer their organizations through constant change. Elite coaching provides expert guidance and an objective perspective to help you navigate these complexities. We partner to develop strategies for managing conflict, aligning</p><span class="more">Read More</span></div>
</section>

<div class="rule"></div>

<section class="closing">
  <h2>Elite Leadership Is<br>The Secret To Lasting<br>Organization Success...</h2>
  <p class="copy">Experience transformative results with a bespoke roadmap, dedicated one-on-one guidance, and confidential, high-impact strategies tailored to your unique vision. Take your organization to new heights—unlock the full potential of your leadership with exclusive Elite Leadership Coaching and Organization Development Consulting.</p>
  <a class="btn" style="left:112px;top:3920px">Book A Discovery Call</a>
  <div class="closing-ring"></div>
  <div class="closing-photo" role="img" aria-label="Portrait photo of Corwin Adeley in front of a mountain landscape"></div>
</section>

<section class="faq">
  <h2>Frequently Asked Questions</h2>
  <p class="intro">Lorem ipsum dolor sit amet, consectetur adipiscing elit, sed do eiusmod tempor incididunt ut labore et dolore magna aliqua. Ut enim ad minim veniam,</p>
  <div class="q" style="top:4362px">Q1. Lorem ipsum dolor sit amet, consectetur adipiscing elit, sed do eiusmod temp</div>
  <div class="q open" style="top:4420px">Q2. Lorem ipsum dolor sit amet, consectetur adipiscing elit, sed do eiusmod temp</div>
  <div class="answer">Lorem ipsum dolor sit amet, consectetur adipiscing elit, sed do eiusmod tempor incididunt ut labore et dolore magna aliqua. Ut enim ad minim veniam,</div>
  <div class="q" style="top:4556px">Q3. Lorem ipsum dolor sit amet, consectetur adipiscing elit, sed do eiusmod temp</div>
  <div class="q" style="top:4616px">Q4. Lorem ipsum dolor sit amet, consectetur adipiscing elit, sed do eiusmod temp</div>
  <div class="q" style="top:4676px">Q5. Lorem ipsum dolor sit amet, consectetur adipiscing elit, sed do eiusmod temp</div>
</section>

<footer>
  <svg class="footer" viewBox="0 0 1200 391" aria-hidden="true">
    <path d="M0 30 Q600 -10 1200 60 L1200 391 L0 391Z" fill="var(--teal)"/>
    <path d="M0 50 Q700 20 1200 40 L1200 391 L0 391Z" fill="var(--gold)"/>
    <path d="M0 60 Q650 40 1200 54 L1200 391 L0 391Z" fill="var(--navy-deep)"/>
  </svg>
  <div class="wordmark foot-brand"><span class="wordmark-dot"></span><span>Keystone Coaching</span></div>
  <nav class="foot-nav"><span>Home</span><span>Coaching</span><span>Retreats</span><span>About</span><span>Insights</span><span>FAQs</span><span>Contact</span></nav>
  <div class="foot-rule"></div>
  <div class="copyright">Copyright © 2025. All rights reserved.</div>
  <div class="social" aria-label="Social profile"></div>
</footer>

</body>
</html>
```